RTavenor Business Cards & Letterhead

I have a logo but need a design for some new business cards. We are a Design-Build Firm that specializes in the design and construction of commercial projects.
the cards need to be professional. no cartoon stuff.
i would like to have the cards in AI format so I can update the card as needed. Logo is provided.
Our Address is: 4187 Marlowe Ct. Fernwood, Colorado 27614

```html
<!DOCTYPE html>
<html lang="en">
<head>
<meta charset="utf-8">
<title>RTavenor Business Card</title>
<link rel="stylesheet" href="https://fonts.googleapis.com/css2?family=Montserrat:wght@400;500;700;800&display=swap">
<style>
  :root {
    --bg: #141414;
    --card-dark: #232323;
    --card-light: #3a3a3a;
    --white: #ffffff;
    --blue: #1a7ac4;
    --text-soft: #e8e8e8;
  }
  * { box-sizing: border-box; margin: 0; padding: 0; }
  html, body {
    width: 1200px; height: 900px; overflow: hidden;
    background: var(--bg);
    font-family: "Montserrat", sans-serif;
  }
  .stage {
    width: 1200px; height: 900px;
    display: flex; flex-direction: column; align-items: center; justify-content: center;
    gap: 40px;
  }
  .card {
    position: relative;
    width: 680px; height: 389px;
    background: linear-gradient(135deg, var(--card-dark) 0%, var(--card-dark) 45%, var(--card-light) 100%);
    box-shadow: 0 10px 28px rgba(0,0,0,.6);
    color: var(--white);
  }
  .brand {
    display: flex; align-items: center; gap: 14px;
    font-weight: 800; letter-spacing: 1px; color: var(--white);
  }
  .brand-mark { background: var(--blue); flex: none; }
  .card-front .brand {
    position: absolute; left: 50%; top: 50%; transform: translate(-50%, -50%);
    font-size: 58px;
  }
  .card-front .brand-mark { width: 46px; height: 46px; }
  .card-back .brand {
    position: absolute; right: 40px; top: 44px;
    font-size: 44px;
  }
  .card-back .brand-mark { width: 36px; height: 36px; }
  .person {
    position: absolute; left: 34px; top: 150px;
    border-left: 12px solid var(--blue);
    padding-left: 14px;
  }
  .person-name {
    color: var(--blue); font-weight: 700; font-size: 28px; letter-spacing: 1.5px; line-height: 1;
  }
  .person-title {
    font-weight: 500; font-size: 17px; letter-spacing: 1.5px; margin-top: 4px; color: var(--text-soft);
  }
  .divider {
    position: absolute; left: 40px; right: 40px; top: 222px;
    height: 2px; background: var(--blue);
  }
  .contacts {
    position: absolute; left: 40px; top: 244px;
    list-style: none; font-size: 17px; color: var(--text-soft);
  }
  .contacts li { display: flex; align-items: center; gap: 12px; height: 32px; }
  .contacts svg { width: 18px; height: 18px; fill: var(--blue); flex: none; }
  .address {
    position: absolute; right: 40px; bottom: 30px;
    text-align: right; font-size: 17px; line-height: 1.45; color: var(--text-soft);
    font-style: normal;
  }
</style>
</head>
<body>
<main class="stage">
  <section class="card card-front">
    <div class="brand"><span class="brand-mark"></span><span class="brand-name">RTAVENOR</span></div>
  </section>

  <section class="card card-back">
    <div class="brand"><span class="brand-mark"></span><span class="brand-name">RTAVENOR</span></div>

    <div class="person">
      <p class="person-name">JORDAN ELLIS</p>
      <p class="person-title">MANAGER</p>
    </div>

    <div class="divider"></div>

    <ul class="contacts">
      <li>
        <svg viewBox="0 0 24 24" aria-hidden="true"><path d="M6.6 10.8a15 15 0 0 0 6.6 6.6l2.2-2.2c.3-.3.7-.4 1-.2 1.1.4 2.3.6 3.6.6.6 0 1 .4 1 1V20c0 .6-.4 1-1 1C10.6 21 3 13.4 3 4c0-.6.4-1 1-1h3.5c.6 0 1 .4 1 1 0 1.3.2 2.5.6 3.6.1.3 0 .7-.2 1z"/></svg>
        <span>123-456-7890</span>
      </li>
      <li>
        <svg viewBox="0 0 24 24" aria-hidden="true"><path d="M2 5h20v2l-10 6L2 7z M2 9l10 6 10-6v10H2z"/></svg>
        <span>info@youremail.com</span>
      </li>
      <li>
        <svg viewBox="0 0 24 24" aria-hidden="true"><path d="M12 2a10 10 0 1 0 0 20 10 10 0 0 0 0-20zm7.9 9h-3.4a15 15 0 0 0-1.4-6.3A8 8 0 0 1 19.9 11zM12 4c1 1.3 2.2 3.7 2.5 7h-5C9.8 7.7 11 5.3 12 4zM8.9 4.7A15 15 0 0 0 7.5 11H4.1a8 8 0 0 1 4.8-6.3zM4.1 13h3.4a15 15 0 0 0 1.4 6.3A8 8 0 0 1 4.1 13zM12 20c-1-1.3-2.2-3.7-2.5-7h5c-.3 3.3-1.5 5.7-2.5 7zm3.1-.7a15 15 0 0 0 1.4-6.3h3.4a8 8 0 0 1-4.8 6.3z"/></svg>
        <span>www.yourwebsite.com</span>
      </li>
    </ul>

    <address class="address">
      4187 Marlowe Ct.<br>
      Fernwood, Colorado 27614
    </address>
  </section>
</main>
</body>
</html>
```